Harbor Ridge Painting Epoxy Flyer

We need a promotional flyer for a new epoxy floor coatings division of our painting company. We do epoxy garage floor coatings and paver sealing. It needs to be based on and very similar to the attached flyer. The garage floor picture needs to look more realistic, and the before and after pavers pictures should look less shiny but still a good contrast. Include attached logo

```html
<!DOCTYPE html>
<html lang="en">
<head>
<meta charset="utf-8">
<title>Harbor Ridge Painting – Epoxy Floor Coatings &amp; Paver Sealing</title>
<link rel="stylesheet" href="https://fonts.googleapis.com/css2?family=Michroma&family=Russo+One&family=Poppins:wght@400;500;600;700&display=swap">
<style>
  :root {
    --orange: #e8800f;
    --orange-deep: #d66f05;
    --blue: #1a73d1;
    --navy: #0d4786;
    --navy-deep: #0a3a70;
    --green: #3a8a2a;
    --green-deep: #1f5c1a;
    --ink: #151515;
    --white: #ffffff;
    --pill-grey: #dcdcdc;
  }
  * { box-sizing: border-box; margin: 0; padding: 0; }
  html, body { width: 938px; height: 1200px; overflow: hidden; background: var(--white); }
  .flyer { position: relative; width: 938px; height: 1200px; background: var(--white); font-family: "Poppins", sans-serif; color: var(--ink); overflow: hidden; }

  /* Header */
  .site-header { position: absolute; left: 0; top: 0; width: 938px; height: 260px; z-index: 2; }
  .brand { position: absolute; left: 60px; top: 110px; display: flex; align-items: center; gap: 12px; }
  .brand-dot { width: 34px; height: 34px; border-radius: 50%; background: var(--green); }
  .brand-name { font-family: "Poppins", sans-serif; font-weight: 600; font-size: 22px; color: var(--ink); white-space: nowrap; }
  .header-rule { position: absolute; left: 385px; top: 58px; width: 2px; height: 212px; background: #444; }
  .headline { position: absolute; left: 415px; top: 52px; }
  .headline-kicker { font-family: "Michroma", sans-serif; font-size: 30px; line-height: 1; color: var(--ink); -webkit-text-stroke: 0.8px var(--ink); }
  .headline-main { font-family: "Russo One", sans-serif; font-weight: 400; font-size: 66px; line-height: 0.98; }
  .headline-main .garage { color: var(--orange); display: block; margin-top: 4px; }
  .headline-main .driveway { color: var(--blue); display: block; }
  .headline-sub { font-family: "Poppins", sans-serif; font-weight: 500; font-size: 25px; line-height: 1.2; margin-top: 0; white-space: nowrap; }

  /* Before / after band */
  .showcase { position: absolute; left: 0; top: 240px; width: 938px; height: 470px; z-index: 1; }
  .label-pill { position: absolute; z-index: 2; height: 44px; border-radius: 22px; background: linear-gradient(#ffffff, var(--pill-grey)); box-shadow: 0 2px 5px rgba(0,0,0,.35); font-family: "Poppins", sans-serif; font-weight: 700; font-size: 30px; line-height: 44px; text-align: center; color: #1b1b1b; letter-spacing: .5px; }
  .label-before { left: 170px; top: 542px; width: 222px; }
  .label-after { left: 499px; top: 543px; width: 225px; }

  /* Services panel */
  .services { position: absolute; left: 0; top: 705px; width: 938px; height: 252px; background: var(--navy); }
  .service-heading { position: absolute; z-index: 2; left: 0; width: 938px; height: 38px; }
  .service-heading .rule { position: absolute; top: 19px; width: 110px; height: 1px; background: rgba(255,255,255,.7); }
  .service-heading .rule.left { left: 182px; }
  .service-heading .rule.right { left: 641px; }
  .service-heading .pill { position: absolute; left: 311px; width: 316px; height: 38px; border-radius: 19px; background: var(--orange); color: var(--white); font-family: "Poppins", sans-serif; font-weight: 700; font-size: 20px; line-height: 38px; text-align: center; }
  .heading-epoxy { top: 637px; }
  .heading-pavers { top: 792px; }

  .feature { position: absolute; z-index: 2; display: flex; align-items: center; }
  .feature-icon { width: 54px; height: 54px; border-radius: 50%; background: var(--white); border: 4px solid var(--green); box-shadow: 0 0 0 2px var(--navy-deep); display: flex; align-items: center; justify-content: center; flex-shrink: 0; }
  .feature-icon.blue-ring { border-color: var(--blue); }
  .feature-icon svg { width: 30px; height: 30px; }
  .feature-text { color: var(--white); font-weight: 500; font-size: 15.5px; line-height: 1.22; margin-left: 12px; white-space: nowrap; }

  /* Tagline banner */
  .tagline { position: absolute; left: 86px; top: 957px; width: 770px; height: 51px; }
  .tagline-text { position: absolute; left: 0; top: 0; width: 770px; height: 46px; line-height: 46px; text-align: center; color: var(--white); font-weight: 700; font-size: 22px; }

  /* Trust row */
  .trust { position: absolute; top: 1026px; display: flex; align-items: center; gap: 9px; }
  .trust svg { width: 34px; height: 38px; }
  .trust-text { font-weight: 500; font-size: 16.5px; line-height: 1.2; color: var(--ink); white-space: nowrap; }
  .trust-rule { position: absolute; top: 1028px; width: 1px; height: 38px; background: #555; }

  /* Call to action */
  .cta { position: absolute; left: 0; top: 1089px; width: 938px; height: 28px; }
  .cta .rule { position: absolute; top: 14px; width: 112px; height: 1px; background: #333; }
  .cta-text { position: absolute; left: 0; width: 938px; text-align: center; font-family: "Michroma", sans-serif; font-size: 20px; line-height: 28px; color: var(--ink); -webkit-text-stroke: 0.6px var(--ink); }
  .cta-text .accent { color: var(--blue); -webkit-text-stroke: 0.6px var(--blue); }
  .phone-badge { position: absolute; left: 67px; top: 1124px; width: 46px; height: 46px; border-radius: 50%; background: var(--blue); display: flex; align-items: center; justify-content: center; }
  .phone-number { position: absolute; left: 124px; top: 1121px; font-family: "Michroma", sans-serif; font-size: 33px; line-height: 52px; color: var(--green-deep); letter-spacing: -1.5px; -webkit-text-stroke: 1.4px var(--green-deep); white-space: nowrap; }
  .phone-rule { position: absolute; left: 492px; top: 1127px; width: 1px; height: 42px; background: #555; }
  .phone-note { position: absolute; left: 503px; top: 1134px; font-size: 17.5px; color: var(--ink); white-space: nowrap; }
</style>
</head>
<body>
<main class="flyer">

  <header class="site-header">
    <div class="brand">
      <span class="brand-dot"></span>
      <span class="brand-name">Harbor Ridge Painting</span>
    </div>
    <div class="header-rule"></div>
    <div class="headline">
      <p class="headline-kicker">Upgrade Your</p>
      <h1 class="headline-main"><span class="garage">Garage</span><span class="driveway">&amp; Driveway</span></h1>
      <p class="headline-sub">From worn-out to like new</p>
    </div>
  </header>

  <svg class="showcase" viewBox="0 0 938 470" xmlns="http://www.w3.org/2000/svg">
    <defs>
      <linearGradient id="beforeTone" x1="0" y1="0" x2="0.6" y2="1">
        <stop offset="0" stop-color="#8a7a62"/>
        <stop offset="0.45" stop-color="#5a5248"/>
        <stop offset="1" stop-color="#3a342e"/>
      </linearGradient>
      <linearGradient id="afterTone" x1="0" y1="0" x2="0" y2="1">
        <stop offset="0" stop-color="#e8e8e6"/>
        <stop offset="0.3" stop-color="#8a8884"/>
        <stop offset="1" stop-color="#5a5754"/>
      </linearGradient>
    </defs>
    <g role="img" aria-label="Before photo: worn, stained concrete garage floor">
      <polygon points="0,0 516,0 381,470 0,470" fill="url(#beforeTone)"/>
    </g>
    <g role="img" aria-label="After photo: freshly coated smooth grey garage floor">
      <polygon points="516,0 938,0 938,470 381,470" fill="url(#afterTone)"/>
    </g>
    <line x1="516" y1="0" x2="381" y2="470" stroke="#ffffff" stroke-width="3"/>

    <path d="M0,0 L938,0 L938,6 Q500,135 63,28 Q30,18 0,9 Z" fill="#ffffff"/>
    <path d="M63,28 Q500,135 938,6 L938,48 Q500,174 63,28 Z" fill="#3a8a2a"/>
    <path d="M63,28 Q500,178 938,52" fill="none" stroke="#ffffff" stroke-width="3"/>

    <path d="M415,190 Q430,272 512,258" fill="none" stroke="#f08a12" stroke-width="13" stroke-linecap="round"/>
    <polygon points="498,232 532,262 500,286" fill="#f08a12"/>

    <path d="M0,378 Q400,290 806,386 Q469,318 0,430 Z" fill="#e8800f"/>
    <path d="M0,430 Q469,290 938,430 L938,470 L0,470 Z" fill="#0d4786"/>
    <path d="M0,430 Q469,290 938,430" fill="none" stroke="#ffffff" stroke-width="4"/>
  </svg>

  <div class="label-pill label-before">BEFORE</div>
  <div class="label-pill label-after">AFTER</div>

  <section class="services" aria-label="Services"></section>

  <div class="service-heading heading-epoxy">
    <span class="rule left"></span><span class="pill">EPOXY FLOOR COATINGS</span><span class="rule right"></span>
  </div>

  <div class="feature" style="left:68px; top:701px;">
    <span class="feature-icon"><svg viewBox="0 0 30 30"><circle cx="15" cy="15" r="11" fill="none" stroke="#e8800f" stroke-width="3"/><path d="M15 8v7l5 3" fill="none" stroke="#e8800f" stroke-width="2.5" stroke-linecap="round"/></svg></span>
    <span class="feature-text">Durable, long<br>lasting finish</span>
  </div>
  <div class="feature" style="left:266px; top:701px;">
    <span class="feature-icon blue-ring"><svg viewBox="0 0 30 30"><path d="M5 25V5h20v6h-7v6h-6v8z" fill="#e8800f"/></svg></span>
    <span class="feature-text">Slip resistant<br>texture</span>
  </div>
  <div class="feature" style="left:466px; top:701px;">
    <span class="feature-icon"><svg viewBox="0 0 30 30"><circle cx="15" cy="15" r="12" fill="#e8800f"/><path d="M8 10l5 4-2 5 6 2M15 14l6-4M17 21l3 3" fill="none" stroke="#ffffff" stroke-width="1.8"/></svg></span>
    <span class="feature-text">Covers cracks &amp;<br>imperfections</span>
  </div>
  <div class="feature" style="left:699px; top:701px;">
    <span class="feature-icon blue-ring"><svg viewBox="0 0 30 30"><circle cx="18" cy="10" r="5" fill="none" stroke="#e8800f" stroke-width="3"/><path d="M4 20h7l5 3h8v3H14l-10-2z" fill="#e8800f"/></svg></span>
    <span class="feature-text">Easy to clean<br>&amp; maintain</span>
  </div>

  <div class="service-heading heading-pavers">
    <span class="rule left"></span><span class="pill">PAVER SEALING</span><span class="rule right"></span>
  </div>

  <div class="feature" style="left:68px; top:855px;">
    <span class="feature-icon"><svg viewBox="0 0 30 30"><circle cx="11" cy="17" r="7" fill="#e8800f"/><path d="M14 22l10-14M19 8h5v5" fill="none" stroke="#e8800f" stroke-width="2.5" stroke-linecap="round"/></svg></span>
    <span class="feature-text">Restores color<br>&amp; enhances<br>appearance</span>
  </div>
  <div class="feature" style="left:274px; top:855px;">
    <span class="feature-icon blue-ring"><svg viewBox="0 0 30 30"><circle cx="15" cy="15" r="6" fill="#e8800f"/><path d="M15 3v4M15 23v4M3 15h4M23 15h4M6.5 6.5l3 3M20.5 20.5l3 3M6.5 23.5l3-3M20.5 9.5l3-3" stroke="#e8800f" stroke-width="2.2" stroke-linecap="round"/></svg></span>
    <span class="feature-text">Protects from<br>sun fading</span>
  </div>
  <div class="feature" style="left:479px; top:855px;">
    <span class="feature-icon"><svg viewBox="0 0 30 30"><rect x="5" y="19" width="20" height="6" fill="#e8800f"/><path d="M8 18l6-10 3 5 4-5v10z" fill="#e8800f"/></svg></span>
    <span class="feature-text">Helps prevent<br>weeds &amp; sand loss</span>
  </div>
  <div class="feature" style="left:731px; top:855px;">
    <span class="feature-icon blue-ring"><svg viewBox="0 0 30 30"><path d="M22 4l-7 11" stroke="#e8800f" stroke-width="2.5" stroke-linecap="round"/><path d="M11 14l7 5-5 7-6-5z" fill="#e8800f"/><path d="M6 9l1 2 2 1-2 1-1 2-1-2-2-1 2-1z" fill="#e8800f"/></svg></span>
    <span class="feature-text">Easier to<br>clean &amp;<br>maintain</span>
  </div>

  <div class="tagline">
    <svg width="770" height="51" viewBox="0 0 770 51" style="position:absolute;left:0;top:0">
      <defs>
        <linearGradient id="taglineTone" x1="0" y1="0" x2="1" y2="0">
          <stop offset="0" stop-color="#1f5c1a"/>
          <stop offset="1" stop-color="#3f9a2e"/>
        </linearGradient>
      </defs>
      <polygon points="0,0 770,0 730,51 40,51" fill="#0d4786"/>
      <polygon points="6,0 764,0 727,46 43,46" fill="url(#taglineTone)"/>
    </svg>
    <p class="tagline-text">Practical upgrades that protect and improve your home</p>
  </div>

  <div class="trust" style="left:175px;">
    <svg viewBox="0 0 34 38"><rect x="2" y="2" width="20" height="28" rx="2" fill="#e8800f"/><path d="M6 9h12M6 14h12M6 19h8" stroke="#fff" stroke-width="2"/><circle cx="25" cy="27" r="7" fill="#fff" stroke="#e8800f" stroke-width="2.5"/><path d="M22 27l2 2 4-4" fill="none" stroke="#e8800f" stroke-width="2"/></svg>
    <span class="trust-text">Licensed<br>&amp; Insured</span>
  </div>
  <span class="trust-rule" style="left:316px;"></span>
  <div class="trust" style="left:337px;">
    <svg viewBox="0 0 34 38"><circle cx="17" cy="7" r="4" fill="#e8800f"/><circle cx="9" cy="16" r="3.5" fill="#e8800f"/><circle cx="17" cy="16" r="3.5" fill="#e8800f"/><circle cx="25" cy="16" r="3.5" fill="#e8800f"/><path d="M4 28q13 -8 26 0l-4 6H8z" fill="#e8800f"/></svg>
    <span class="trust-text">Family-Owned<br>Local Business</span>
  </div>
  <span class="trust-rule" style="left:532px;"></span>
  <div class="trust" style="left:547px;">
    <svg viewBox="0 0 34 38"><path d="M17 2a11 11 0 0 1 11 11c0 8-11 20-11 20S6 21 6 13A11 11 0 0 1 17 2z" fill="#e8800f"/><circle cx="17" cy="13" r="4.5" fill="#fff"/><ellipse cx="17" cy="35" rx="11" ry="2.5" fill="#e8800f"/></svg>
    <span class="trust-text">Serving Prescott &amp;<br>Surrounding Areas</span>
  </div>

  <div class="cta">
    <span class="rule" style="left:141px;"></span>
    <p class="cta-text">CALL FOR A <span class="accent">FREE ESTIMATE</span></p>
    <span class="rule" style="left:685px;"></span>
  </div>

  <div class="phone-badge">
    <svg width="26" height="26" viewBox="0 0 24 24"><path d="M6.6 10.8a15 15 0 0 0 6.6 6.6l2.2-2.2a1 1 0 0 1 1-.25 11.4 11.4 0 0 0 3.6.57 1 1 0 0 1 1 1V20a1 1 0 0 1-1 1A17 17 0 0 1 3 4a1 1 0 0 1 1-1h3.5a1 1 0 0 1 1 1c0 1.25.2 2.45.57 3.57a1 1 0 0 1-.25 1z" fill="#ffffff"/></svg>
  </div>
  <p class="phone-number">928-555-0142</p>
  <span class="phone-rule"></span>
  <p class="phone-note">Fast, professional service you can trust</p>

</main>
</body>
</html>
```